I have a logo and need to design the business card and stationery.
Updates

The uploaded logo image named as GREYMARSH CONTRACTS which is to be replaced to GREYMARSH CONTRACTS. Kindly add below details and submit the designs- Company name- Greymarsh Engineering Contracts LLP Name & Post- Kelvan Joshi (Designated Partner) Address- Block No.317, Wing C, Tulvo Trade Court, Manek Pural Road, Ruparel Industrial Estate, Goregaon(E), Mumbai - 400 063 Contact- +91 97415 60382 Email- kelvanjoshi@mailbrook.example Website- www.greymarshcontracts.example Contact for Letterhead- +91-22-28754193

Hi Tovin Rahul, We are liking your Design #28860835. We have suggested some changes which are mentioned in feedback. Kindly revert with it asap to finalize this design.

Colors

Designer to choose colors to be used in the design.

```html
<!DOCTYPE html>
<html lang="en">
<head>
<meta charset="utf-8">
<title>Greymarsh Contracts – Business Card</title>
<link href="https://fonts.googleapis.com/css2?family=Montserrat:wght@400;500;600;700&display=swap" rel="stylesheet">
<style>
  :root {
    --backdrop: #a9aaa5;
    --card-front: #353535;
    --card-back: #262626;
    --pattern-light: #3a3a3a;
    --pattern-dark: #1c1c1c;
    --ink: #ffffff;
    --ink-soft: #e6e6e6;
    --rule: #bdbdbd;
  }
  * { margin: 0; padding: 0; box-sizing: border-box; }
  html, body { width: 1200px; height: 801px; overflow: hidden; }
  body {
    background: var(--backdrop);
    font-family: "Montserrat", sans-serif;
    display: flex;
    align-items: center;
    justify-content: center;
    gap: 40px;
  }
  .card {
    width: 540px;
    height: 309px;
    position: relative;
    box-shadow: 0 10px 24px rgba(0,0,0,0.25);
    overflow: hidden;
  }
  .card--front {
    background: var(--card-front);
    display: flex;
    align-items: center;
  }
  .card--back {
    background: var(--card-back);
    display: flex;
    align-items: center;
    justify-content: center;
  }
  .brand {
    width: 240px;
    flex: none;
    display: flex;
    flex-direction: column;
    align-items: center;
    gap: 14px;
    color: var(--ink);
  }
  .brand__square { width: 52px; height: 52px; background: var(--ink); }
  .brand__name { font-weight: 600; text-align: center; line-height: 1.25; }
  .brand__name .line-main { display: block; font-size: 25px; letter-spacing: 1px; }
  .brand__name .line-sub { display: block; font-size: 13px; letter-spacing: 7px; margin-right: -7px; }
  .divider {
    width: 1px;
    height: 170px;
    flex: none;
    background: var(--rule);
  }
  .contact {
    padding-left: 22px;
    padding-right: 16px;
    color: var(--ink-soft);
    font-size: 10.5px;
    line-height: 1.5;
  }
  .contact__name {
    font-size: 18px;
    font-weight: 600;
    color: var(--ink);
    letter-spacing: 0.5px;
    line-height: 1.3;
  }
  .contact__role {
    font-size: 11px;
    letter-spacing: 0.5px;
    margin-bottom: 10px;
  }
  .contact__address { margin-bottom: 6px; }
  .contact__row { display: flex; align-items: center; gap: 6px; }
  .contact__row svg { width: 10px; height: 10px; flex: none; }
  .pattern-field {
    position: absolute;
    inset: 0;
    background: linear-gradient(160deg, var(--pattern-dark) 0%, var(--pattern-light) 55%, var(--pattern-dark) 100%);
  }
  .back-mark {
    position: relative;
    display: flex;
    align-items: center;
    gap: 10px;
    color: var(--ink);
    font-weight: 600;
    font-size: 20px;
    letter-spacing: 1px;
  }
  .back-mark__square { width: 22px; height: 22px; background: var(--ink); }
</style>
</head>
<body>

  <section class="card card--front">
    <div class="brand">
      <div class="brand__square"></div>
      <div class="brand__name">
        <span class="line-main">GREYMARSH</span>
        <span class="line-sub">CONTRACTS</span>
      </div>
    </div>
    <div class="divider"></div>
    <div class="contact">
      <div class="contact__name">KELVAN JOSHI</div>
      <div class="contact__role">DESIGNATED PARTNER</div>
      <div class="contact__address">
        Block No.317, Wing C, Tulvo Trade Court,<br>
        Manek Pural Road,<br>
        Ruparel Industrial Estate,<br>
        Goregaon(E), Mumbai - 400 063
      </div>
      <div class="contact__row">
        <svg viewBox="0 0 10 10"><path d="M2 0.8 L3.6 2.8 L2.8 3.8 Q4 6 6.2 7.2 L7.2 6.4 L9.2 8 L8 9.4 Q4 9 1.2 5 Q0.4 2.6 2 0.8Z" fill="#e6e6e6"/></svg>
        <span>+91 97415 60382</span>
      </div>
      <div class="contact__row">
        <svg viewBox="0 0 10 10"><rect x="0.8" y="2" width="8.4" height="6" fill="none" stroke="#e6e6e6" stroke-width="1"/><path d="M0.8 2 L5 5.4 L9.2 2" fill="none" stroke="#e6e6e6" stroke-width="1"/></svg>
        <span>kelvanjoshi@mailbrook.example</span>
      </div>
      <div class="contact__row">
        <svg viewBox="0 0 10 10"><circle cx="5" cy="5" r="4.2" fill="none" stroke="#e6e6e6" stroke-width="1"/><ellipse cx="5" cy="5" rx="1.8" ry="4.2" fill="none" stroke="#e6e6e6" stroke-width="0.8"/><line x1="0.8" y1="5" x2="9.2" y2="5" stroke="#e6e6e6" stroke-width="0.8"/></svg>
        <span>www.greymarshcontracts.example</span>
      </div>
    </div>
  </section>

  <section class="card card--back">
    <div class="pattern-field" role="img" aria-label="Repeating embossed brand-mark pattern in dark grey tones"></div>
    <div class="back-mark">
      <span class="back-mark__square"></span>
      <span>GREYMARSH</span>
    </div>
  </section>

</body>
</html>
```